Provide bookkeeping and accounting services to small and growing businesses

We need website and logo design using the name Dornaby as the logo.
The target audience are small companies and startups who need:
1) Simple bookkeeping services
2) Accounting advice that only someone with many years of senior financial experience as a CPA can provide.

The services are provided by two individuals. each of whom specialize in one of the areas.

We want the website to be clean without a lot of visual distraction but don't know how to make a boring subject interesting. We believe our potential clients, small business owners, need to find what they want quickly and easily without a lot of verbiage or distractions.

We've attached a draft of the homepage and have completed the text on most of the other pages.

Target Market(s)

small and early stage growth companies in San Diego North County

Industry/Entity Type

Accounting

Number of Pages Required

1 page

Font styles to use
Sans Serif

Colors
86cfc6
33b8a4
85cae6

Requirements
Must have
• We need a design for the website homepage that includes the name Dornaby as the logo. Must include a design for the name.
• Must have color in teal or greenish blue.
Nice to have
• White background, clean, clear, uncluttered.
• We would like to use the design in a Theme on a WordPress website. Themes Paper Lantern and Quiet Harbour are appealing to us.
Should not have
• Moving pictures

```html
<!DOCTYPE html>
<html lang="en">
<head>
<meta charset="utf-8">
<title>Dornaby Accounting &amp; Bookkeeping</title>
<link href="https://fonts.googleapis.com/css2?family=Roboto:wght@300;400;500&family=Open+Sans:ital,wght@0,400;0,600;1,400;1,600&display=swap" rel="stylesheet">
<style>
:root{
  --teal:#33b8a4;
  --teal-soft:#86cfc6;
  --sky:#85cae6;
  --ink:#333a3f;
  --body:#555b60;
  --muted:#8a9095;
  --light:#f2f3f3;
  --white:#ffffff;
  --dark-green:#17241d;
  --bar:#2f3233;
}
*{margin:0;padding:0;box-sizing:border-box}
html,body{width:1200px;height:2514px;overflow:hidden}
body{font-family:'Open Sans',sans-serif;color:var(--body);background:var(--white);position:relative}
.heading{font-family:'Roboto',sans-serif;font-weight:400}

/* header */
.site-header{position:absolute;top:0;left:0;width:1200px;height:96px;background:var(--white)}
.brand{position:absolute;left:98px;top:20px;display:flex;align-items:center;gap:12px}
.brand-dot{width:54px;height:54px;border-radius:50%;background:var(--teal)}
.brand-name{font-family:'Roboto',sans-serif;font-weight:500;font-size:30px;color:var(--ink);letter-spacing:1px;line-height:1}
.brand-tag{font-size:13px;color:var(--ink);margin-top:3px}
.main-nav{position:absolute;right:100px;top:40px;display:flex;gap:44px;font-family:'Roboto',sans-serif;font-size:14px;color:#555}
.main-nav .active{color:var(--teal)}

/* hero */
.hero{position:absolute;top:96px;left:0;width:1200px;height:550px;background:linear-gradient(120deg,#c9ccd0 0%,#8d949b 35%,#3e4853 65%,#1c2a3d 100%)}
.hero-title{position:absolute;left:610px;top:248px;font-family:'Roboto',sans-serif;font-weight:500;font-size:40px;line-height:44px;color:var(--white)}
.hero-arrow{position:absolute;top:240px}
.hero-arrow.prev{left:34px}
.hero-arrow.next{right:34px}

/* welcome */
.welcome{position:absolute;top:646px;left:0;width:1200px;height:216px;background:var(--teal);text-align:center;color:var(--white)}
.welcome h1{font-size:31px;margin-top:46px}
.welcome p{width:900px;margin:18px auto 0;font-size:11.5px;line-height:20px}

/* services */
.services{position:absolute;top:862px;left:0;width:1200px;height:536px;background:var(--light)}
.section-title{font-size:40px;color:var(--ink);text-align:center;margin-top:48px}
.title-rule{width:76px;height:2px;background:var(--teal);margin:14px auto 0}
.service{position:absolute;top:142px;width:320px}
.service-head{display:flex;align-items:flex-start;gap:10px;height:60px}
.service-head h3{font-family:'Roboto',sans-serif;font-weight:400;font-size:19px;color:var(--ink);line-height:22px}
.service-head span{font-size:11px;color:var(--ink)}
.service-photo{margin-top:8px;width:320px;height:184px;border:4px solid #e3e5e6;background:var(--white);padding:2px}
.service-photo div{width:100%;height:100%}
.service p{margin-top:22px;font-size:11.5px;line-height:21px}

/* about */
.about{position:absolute;top:1398px;left:0;width:1200px;height:454px;background:var(--white)}
.about-visual{position:absolute;left:130px;top:70px;width:405px;height:330px;background:radial-gradient(ellipse at 45% 50%,#dfe4ea 0%,#f2f4f6 60%,#ffffff 100%)}
.about-text{position:absolute;left:588px;top:104px;width:480px}
.about-text h2{font-size:32px;line-height:38px;color:var(--ink)}
.about-text p{font-size:11.5px;line-height:22px;margin-top:22px}

/* testimonial */
.testimonial{position:absolute;top:1852px;left:0;width:1200px;height:320px;background:var(--dark-green)}
.avatar{position:absolute;left:156px;top:92px;width:142px;height:142px;border-radius:50%;border:4px solid var(--white);background:linear-gradient(160deg,#d7dde3,#8e9aa6)}
.quote-mark{position:absolute;left:152px;top:92px;width:38px;height:38px;border-radius:50%;background:#2a2f30;border:3px solid var(--white)}
.testimonial h2{position:absolute;left:338px;top:74px;font-size:31px;color:var(--white)}
.testimonial blockquote{position:absolute;left:340px;top:130px;width:720px;font-style:italic;font-size:13.5px;line-height:22px;color:var(--white)}
.testimonial cite{position:absolute;left:342px;top:214px;font-style:italic;font-size:14px;color:var(--white)}
.testimonial cite b{font-weight:600}

/* footer */
.site-footer{position:absolute;top:2172px;left:0;width:1200px;height:281px;background:var(--light)}
.footer-brand{position:absolute;left:96px;top:96px;width:140px;text-align:center}
.footer-brand .brand-dot{width:58px;height:58px;margin:0 auto}
.footer-brand .brand-name{font-size:23px;margin-top:8px}
.footer-brand .brand-tag{font-size:11px}
.footer-col h4{font-size:17px;color:var(--ink);margin-bottom:14px}
.newsletter{position:absolute;left:315px;top:56px;width:263px}
.newsletter p{font-size:11px;line-height:18px;margin-bottom:12px}
.field{height:40px;background:var(--white);font-size:11px;color:#555;padding:12px 14px;margin-bottom:10px}
.field-row{display:flex}
.field-row .field{flex:1}
.subscribe{width:98px;height:40px;background:var(--teal);color:var(--white);font-size:12px;text-align:center;line-height:40px}
.contacts{position:absolute;left:686px;top:56px}
.contact-item{display:flex;gap:12px;font-size:12.5px;line-height:19px;margin-bottom:12px;color:#666}
.quick-links{position:absolute;left:1000px;top:56px}
.quick-links ul{list-style:none;font-size:11px;line-height:22px;color:#666}
.copyright{position:absolute;top:2453px;left:0;width:1200px;height:61px;background:var(--bar);color:#d9dcdd;font-size:11.5px;text-align:center;line-height:61px}
</style>
</head>
<body>

<header class="site-header">
  <div class="brand">
    <div class="brand-dot"></div>
    <div>
      <div class="brand-name">DORNABY</div>
      <div class="brand-tag">Accounting &amp; Bookkeeping</div>
    </div>
  </div>
  <nav class="main-nav">
    <span class="active">HOME</span><span>ABOUT US</span><span>SERVICES</span><span>EXPERIENCE</span><span>RESOURCES</span><span>CONTACT US</span>
  </nav>
</header>

<section class="hero" role="img" aria-label="Photo of a business meeting with a hand holding a pen over a tablet and financial charts">
  <svg class="hero-arrow prev" width="24" height="60" viewBox="0 0 24 60"><path d="M22 2 L2 30 L22 58" fill="none" stroke="rgba(255,255,255,.5)" stroke-width="2"/></svg>
  <h2 class="hero-title">DORNABY ACCOUNTING<br>&amp; BOOKKEEPING</h2>
  <svg class="hero-arrow next" width="24" height="60" viewBox="0 0 24 60"><path d="M2 2 L22 30 L2 58" fill="none" stroke="#ffffff" stroke-width="2"/></svg>
</section>

<section class="welcome">
  <h1 class="heading">WELCOME TO DORNABY ACCOUNTING</h1>
  <p>Dornaby offers a flexible range of accounting and bookkeeping services and support for small and growing organizations in San Diego North County. We provide bookkeeping services specializing in LedgerDesk® at your offices or remotely from ours. We also provide a broad range of accounting services or financial advice. Nemo enim ipsam voluptatem quia voluptas sit aspernatur aut odit aut fugit, sed quia consequuntur magni dolores eos qui ratione voluptatem sequi nesciunt.</p>
</section>

<section class="services">
  <h2 class="heading section-title">Our Services</h2>
  <div class="title-rule"></div>

  <article class="service" style="left:98px">
    <div class="service-head">
      <svg width="42" height="38" viewBox="0 0 42 38"><rect x="1" y="2" width="40" height="26" rx="2" fill="var(--teal)"/><rect x="5" y="6" width="32" height="18" fill="#fff"/><rect x="18" y="28" width="6" height="5" fill="var(--teal)"/><rect x="11" y="33" width="20" height="3" fill="var(--teal)"/></svg>
      <div><h3>Book Keeping Services</h3><span>Lorem ipsum dolor sit amet,</span></div>
    </div>
    <div class="service-photo"><div role="img" aria-label="Photo of hands using a tablet beside paperwork" style="background:linear-gradient(135deg,#e8eef3,#9fb3c5 55%,#4f6476)"></div></div>
    <p>Lorem ipsum dolor sit amet, consectetur adipisicing elit, sed do eiusmod tempor incididunt ut labore et dolore magna aliqua. Ut enim ad minim veniam,</p>
  </article>

  <article class="service" style="left:440px">
    <div class="service-head">
      <svg width="34" height="38" viewBox="0 0 34 38"><path d="M11 2 H23 L19 9 H15 Z" fill="var(--teal)"/><path d="M15 10 H19 C30 14 33 26 31 32 C30 36 27 37 17 37 C7 37 4 36 3 32 C1 26 4 14 15 10 Z" fill="var(--teal)"/><text x="17" y="31" font-family="Roboto,sans-serif" font-size="15" fill="#fff" text-anchor="middle">$</text></svg>
      <div><h3>Financial Planning</h3><span>Lorem ipsum dolor sit amet,</span></div>
    </div>
    <div class="service-photo"><div role="img" aria-label="Photo of a hand touching glowing dollar symbols over a bar chart" style="background:linear-gradient(135deg,#a9bfdc,#54709b 55%,#2c3e63)"></div></div>
    <p>Lorem ipsum dolor sit amet, consectetur adipisicing elit, sed do eiusmod tempor incididunt ut labore et dolore magna aliqua. Ut enim ad minim veniam,</p>
  </article>

  <article class="service" style="left:782px">
    <div class="service-head">
      <svg width="40" height="34" viewBox="0 0 40 34"><circle cx="20" cy="8" r="6" fill="var(--teal)"/><circle cx="8" cy="11" r="5" fill="var(--teal)"/><circle cx="32" cy="11" r="5" fill="var(--teal)"/><path d="M10 32 C10 20 30 20 30 32 Z" fill="var(--teal)"/><path d="M0 30 C0 19 14 18 12 24 L9 30 Z" fill="var(--teal)"/><path d="M40 30 C40 19 26 18 28 24 L31 30 Z" fill="var(--teal)"/></svg>
      <div><h3>Accounting Advice</h3><span>Lorem ipsum dolor sit amet,</span></div>
    </div>
    <div class="service-photo"><div role="img" aria-label="Photo of two people reviewing documents at a desk" style="background:linear-gradient(135deg,#f1f3f5,#c3ccd5 55%,#6f7f8f)"></div></div>
    <p>Lorem ipsum dolor sit amet, consectetur adipisicing elit, sed do eiusmod tempor incididunt ut labore et dolore magna aliqua. Ut enim ad minim veniam,</p>
  </article>
</section>

<section class="about">
  <div class="about-visual" role="img" aria-label="Illustration of a laptop showing financial dashboards with a colourful 3D bar chart, pie chart and smartphone"></div>
  <div class="about-text">
    <h2 class="heading">DORNABY ACCOUNTING<br>&amp; BOOKKEEPING</h2>
    <p>Lorem ipsum dolor sit amet, consectetur adipiscing elit, sed do eiusmod tempor incididunt ut labore et dolore magna aliqua. Ut enim ad minim veniam, quis nostrud exercitation ullamco laboris nisi ut aliquip ex ea commodo consequat.</p>
    <p>Lorem ipsum dolor sit amet, consectetur adipiscing elit, sed do eiusmod tempor incididunt ut labore et dolore magna aliqua. Ut enim ad minim veniam, quis nostrud exercitation ullamco laboris nisi ut aliquip ex ea commodo consequat.</p>
  </div>
</section>

<section class="testimonial">
  <div class="avatar" role="img" aria-label="Portrait photo of the quoted client"></div>
  <div class="quote-mark"><svg width="32" height="32" viewBox="0 0 32 32"><text x="16" y="27" font-family="Georgia,serif" font-size="26" fill="#fff" text-anchor="middle">“</text></svg></div>
  <h2 class="heading">SATISFIED CUSTOMERS</h2>
  <blockquote>“ Lorem ipsum dolor sit amet, consectetur adipiscing elit, sed do eiusmod tempor incididunt ut labore et dolore magna aliqua. Ut enim ad minim veniam, quis nostrud exercitation ullamco laboris nisi ut aliquip ex ea commodo consequat. Duis aute irure dolor in reprehenderit in voluptate velit esse cillum dolore eu fugiat nulla pariatur. ”</blockquote>
  <cite><b>Alex Marlow</b> - Managing Partner</cite>
</section>

<footer class="site-footer">
  <div class="footer-brand">
    <div class="brand-dot"></div>
    <div class="brand-name">DORNABY</div>
    <div class="brand-tag">Accounting &amp; Bookkeeping</div>
  </div>

  <div class="footer-col newsletter">
    <h4 class="heading">SIGN UP FOR NEWSLETTER</h4>
    <p>Excepteur sint occaecat cupidatat non proident, sunt in culpa qui officia deserunt</p>
    <div class="field">Enter Name</div>
    <div class="field-row"><div class="field">Enter Email</div><div class="subscribe">SUBSCRIBE</div></div>
  </div>

  <div class="footer-col contacts">
    <h4 class="heading">CONTACTS US</h4>
    <div class="contact-item"><svg width="14" height="18" viewBox="0 0 14 18"><path d="M7 1 C3 1 1 4 1 7 C1 11 7 17 7 17 C7 17 13 11 13 7 C13 4 11 1 7 1 Z" fill="#b0b4b7"/><circle cx="7" cy="7" r="2.3" fill="#f2f3f3"/></svg><span>14 Harbour Lane, Westbrook<br>San Diego North County</span></div>
    <div class="contact-item"><svg width="14" height="14" viewBox="0 0 14 14"><path d="M3 1 L5 4 L4 6 C5 8 6 9 8 10 L10 9 L13 11 L11 13 C6 13 1 8 1 3 Z" fill="#b0b4b7"/></svg><span>Phone: (555) 014-2290</span></div>
    <div class="contact-item"><svg width="14" height="12" viewBox="0 0 14 12"><rect x="1" y="2" width="12" height="9" fill="#b0b4b7"/><path d="M1 2 L7 7 L13 2" fill="none" stroke="#f2f3f3" stroke-width="1.2"/></svg><span>info@dornabyaccounting.com</span></div>
  </div>

  <div class="footer-col quick-links">
    <h4 class="heading">QUICK LINKS</h4>
    <ul><li>Home</li><li>About Us</li><li>Services</li><li>Experience</li><li>Resources</li><li>Contact Us</li></ul>
  </div>
</footer>

<div class="copyright">©2015 - 2016 Dornaby Accounting &amp; Bookkeeping, All Rights Reserved.</div>

</body>
</html>
```